Website for virtual assistant and proofreader

Professional, feminine (but not flowery!) website offering and explaining my services as a VA and Proofreader. Probably only 7 pages: home, about, services (x2), fees, testimonials and contact page. <br/><br/>I already have most of the content, which I have uploaded so you can get an idea of waht I do. I have brand colours and logo already also uploaded. I really just need the bones of the site to be designed and am happy/capable of setting this up as a Wordpress site. I'm just rubbish at design!

Industry/Entity Type

Business Service

Coding

Coded - Design and coding required

Number of Pages Required

4 page

Other font styles liked:
• Roboto Bold + Great Vibes

Colors
3276b5
fee3d4

Requirements
Must have
• should be informative, professional, feminine. Clean, clear, CTA's links to services and fees pages
• Also, see all 3 colour codes on the attached doc.
Nice to have
• business images but place holders will do
Should not have
• Nothing flowery or cartoons! Not 'busy'

```html
<!DOCTYPE html>
<html lang="en">
<head>
<meta charset="utf-8">
<title>Maren K Holt – Virtual Assistant and Proofreader</title>
<link rel="stylesheet" href="https://fonts.googleapis.com/css2?family=Great+Vibes&family=Roboto:wght@400;500;700&display=swap">
<style>
:root{
  --blue:#3276b5;
  --navy:#1a5a8c;
  --navy-deep:#17548a;
  --pink:#fee3d4;
  --peach:#f0b9a2;
  --peach-band:#efc1b0;
  --taupe:#7d7371;
  --ink:#3c3c3c;
  --white:#ffffff;
  --line:#cfd7df;
}
*{margin:0;padding:0;box-sizing:border-box}
html,body{width:1200px;height:4552px;overflow:hidden}
body{font-family:'Roboto',Arial,sans-serif;color:var(--ink);background:var(--white);position:relative}
.abs{position:absolute}
.script{font-family:'Great Vibes',cursive;font-weight:400}
.btn{position:absolute;display:flex;align-items:center;justify-content:center;border-radius:30px;font-weight:700;font-size:15px;color:#2b2b2b;background:var(--peach);text-decoration:none}
.btn-outline{background:var(--white);border:2px solid var(--navy);color:var(--navy)}

/* header */
.site-header{position:absolute;left:0;top:0;width:1200px;height:104px;background:var(--white)}
.brand{position:absolute;left:132px;top:24px;display:flex;align-items:center;gap:12px}
.brand-mark{width:30px;height:30px;border-radius:50%;background:var(--blue)}
.brand-name{font-size:30px;font-weight:500;color:var(--blue);line-height:1}
.brand-tag{position:absolute;left:174px;top:66px;font-size:12px;font-weight:500;color:var(--navy)}
.main-nav{position:absolute;left:480px;top:0;height:104px;display:flex;gap:0}
.main-nav a{display:flex;align-items:center;height:104px;padding:0 14px;font-size:15px;font-weight:500;color:var(--blue);text-decoration:none;position:relative}
.main-nav a.active{color:var(--navy)}
.main-nav a.active::before{content:"";position:absolute;left:0;right:0;top:0;height:4px;background:var(--navy)}

/* hero */
.hero{position:absolute;left:0;top:104px;width:1200px;height:603px;overflow:hidden}
.hero-photo{position:absolute;inset:0;background:linear-gradient(110deg,#c69a63 0%,#9b7752 30%,#6f6a6e 60%,#8f8f9b 80%,#6b5a4c 100%)}
.hero-bubble{position:absolute;left:117px;top:77px;width:406px;height:406px;border-radius:50%;background:rgba(24,88,140,.9);text-align:center;color:var(--white)}
.hero-bubble h1{font-family:'Great Vibes',cursive;font-weight:400;font-size:76px;margin-top:90px;line-height:1}
.hero-bubble p{font-size:24px;line-height:31px;margin-top:14px}
.hero-bubble .btn{left:116px;top:280px;width:178px;height:44px}
.hero-dots{position:absolute;left:557px;top:559px;display:flex;gap:8px}
.hero-dots span{width:13px;height:13px;border-radius:50%;background:var(--white)}
.hero-dots span.current{background:transparent;border:2px solid var(--white)}

/* about */
.about-photo{position:absolute;left:154px;top:783px;width:358px;height:385px;border-radius:0 70px 0 70px;background:linear-gradient(160deg,#b9a08a,#9d7460 55%,#d8c4b2)}
.about-title{position:absolute;left:565px;top:790px;font-size:40px;font-weight:400;color:var(--navy)}
.about-copy{position:absolute;left:565px;top:865px;width:550px;font-size:13.5px;line-height:23px;color:#4a4a4a}
.about-copy p+p{margin-top:26px}

/* services */
.services{position:absolute;left:0;top:1267px;width:1200px;height:566px;background:var(--navy)}
.services h2{position:absolute;top:58px;width:100%;text-align:center;font-size:37px;font-weight:400;color:var(--white)}
.services .lead{position:absolute;top:112px;left:180px;width:840px;text-align:center;font-size:14px;line-height:23px;color:var(--white)}
.service-card{position:absolute;top:191px;width:226px;height:313px;border:1px solid #8fb2d2;color:var(--white);text-align:center}
.service-card svg{display:block;margin:30px auto 0}
.service-card h3{font-size:16px;font-weight:700;line-height:23px;margin-top:16px;padding:0 12px}
.service-card p{font-size:12.5px;line-height:22px;margin-top:12px;padding:0 20px;color:#e3edf6}
.service-card .btn{top:255px;width:96px;height:32px;font-size:11px}
.service-card .btn-outline{left:12px;background:transparent;border:2px solid var(--white);color:var(--white)}
.service-card .btn-contact{left:118px}

/* quote band */
.quote-band{position:absolute;left:0;top:1833px;width:1200px;height:254px;background:linear-gradient(180deg,#f3cdbd 0%,#eab6a3 60%,#e6a995 100%)}
.quote-band p{position:absolute;width:100%;text-align:center;color:#3a3a3a;font-size:54px;line-height:1}
.quote-band .l1{top:65px}
.quote-band .l2{top:118px;left:40px}

/* feature rows */
.feature-photo{position:absolute}
.feature-frame{position:absolute;border:1.5px solid #9a9a9a}
.feature-card{position:absolute;background:var(--white);box-shadow:0 4px 30px rgba(0,0,0,.12);padding:40px 50px 0}
.feature-card h3{font-size:23px;font-weight:700;color:var(--navy)}
.feature-card p{font-size:13.5px;line-height:24px;margin-top:18px;color:#444}
.feature-card .btn{position:static;display:inline-flex;width:146px;height:38px;font-size:13px;margin-top:22px}

/* calling */
.calling{position:absolute;left:0;top:3539px;width:1200px;height:407px;background:var(--taupe);text-align:center;color:var(--white)}
.calling h2{font-family:'Great Vibes',cursive;font-weight:400;font-size:48px;margin-top:82px}
.calling p{font-size:17.5px;line-height:27px;width:860px;margin:22px auto 0}
.calling .btn{left:516px;top:272px;width:158px;height:43px}

/* testimonials */
.testimonials h2{position:absolute;top:4000px;width:100%;text-align:center;font-size:24px;font-weight:700;color:#2f2f2f}
.quote-card{position:absolute;top:4085px;width:429px;height:205px;border:1.5px solid #8a8a8a;text-align:center;padding-top:56px}
.quote-card p{font-size:15px;line-height:29px;color:#333}
.quote-card .author{font-weight:700;margin-top:2px}
.avatar{position:absolute;top:-30px;left:177px;width:74px;height:74px;border-radius:50%;background:linear-gradient(160deg,#a68b78,#5e4c43)}
.slider-arrow{position:absolute;top:4163px}

/* footer */
.site-footer{position:absolute;left:0;top:4368px;width:1200px;height:184px;background:var(--navy-deep);color:var(--white);text-align:center}
.footer-nav{display:flex;justify-content:center;gap:40px;margin-top:40px}
.footer-nav a{color:var(--white);text-decoration:none;font-size:16.5px;font-weight:500}
.legal{font-size:12px;margin-top:14px}
.social{display:flex;justify-content:center;gap:6px;margin-top:18px}
.social span{width:34px;height:34px;border:1.5px solid var(--white);border-radius:50%;display:flex;align-items:center;justify-content:center}
.social span i{width:12px;height:12px;background:var(--white);border-radius:50%}
</style>
</head>
<body>

<header class="site-header">
  <div class="brand"><span class="brand-mark"></span><span class="brand-name">Maren K Holt</span></div>
  <div class="brand-tag">Virtual Assistant and Proofreader</div>
  <nav class="main-nav">
    <a class="active" href="#">HOME</a>
    <a href="#">ABOUT</a>
    <a href="#">SERVICES</a>
    <a href="#">FEES</a>
    <a href="#">TESTIMONIALS</a>
    <a href="#">CONTACT</a>
  </nav>
</header>

<section class="hero">
  <div class="hero-photo" role="img" aria-label="Hands typing on a laptop at a sunlit wooden table"></div>
  <div class="hero-bubble">
    <h1>Allow me...</h1>
    <p>to handle the details so you can<br>get on with business.</p>
    <a class="btn" href="#">Learn More</a>
  </div>
  <div class="hero-dots"><span class="current"></span><span></span><span></span><span></span></div>
</section>

<section class="about">
  <div class="about-photo" role="img" aria-label="Portrait of the virtual assistant"></div>
  <h2 class="about-title">About Maren K Holt</h2>
  <div class="about-copy">
    <p>Every great leader is backed by diligent and knowledgeable support. Have you ever wondered what it would be like to have your very own personal assistant? Well, you can. A virtual assistant can do everything a full-time assistant can, with the added bonus that she can save you money.</p>
    <p>Whether you need daily help, or help with special assignments or big projects, hiring me as your VA will save you the costs typically associated with an employee–holiday pay, sick pay, overtime, taxes, and insurance, are no longer your concern. And, as a virtual assistant, I only charge for the hours I actually work–no more resource-siphoning downtime.</p>
  </div>
  <a class="btn" href="#" style="left:565px;top:1129px;width:177px;height:43px">Learn More</a>
  <a class="btn btn-outline" href="#" style="left:755px;top:1129px;width:176px;height:43px">Contact</a>
</section>

<section class="services">
  <h2>Our Services</h2>
  <p class="lead">Do you need some Smart Office Support (SOS)? Do you have a huge project looming on the horizon? Do you just need a little support managing the growing stacks of To-Dos cluttering your desk?</p>

  <div class="service-card" style="left:134px">
    <svg width="64" height="64" viewBox="0 0 64 64" fill="none" stroke="#fff" stroke-width="2"><circle cx="34" cy="26" r="14"/><circle cx="34" cy="26" r="6"/><path d="M20 30c-4 6-6 10-2 12h4v10h14v-6"/></svg>
    <h3>Organizational/Project Management</h3>
    <p>Reliable project and team management, master of organisation</p>
    <a class="btn btn-outline" href="#">Learn More</a><a class="btn btn-contact" href="#">Contact</a>
  </div>
  <div class="service-card" style="left:373px">
    <svg width="64" height="64" viewBox="0 0 64 64" fill="none" stroke="#fff" stroke-width="2"><rect x="8" y="10" width="30" height="46"/><rect x="14" y="16" width="18" height="8"/><path d="M14 30h6M26 30h6M14 38h6M26 38h6M14 46h6M26 46h6"/><rect x="42" y="10" width="14" height="46"/></svg>
    <h3>Administrative and Accounting Support</h3>
    <p>Work smarter not harder with the right VA by your side</p>
    <a class="btn btn-outline" href="#">Learn More</a><a class="btn btn-contact" href="#">Contact</a>
  </div>
  <div class="service-card" style="left:610px">
    <svg width="64" height="64" viewBox="0 0 64 64" fill="none" stroke="#fff" stroke-width="2"><rect x="8" y="10" width="48" height="36"/><path d="M8 18h48M16 26h16M16 32h24M16 38h12M26 46v8M38 46v8M20 54h24"/></svg>
    <h3>Website Admininstration</h3>
    <p>Dependable and reliable website updates–like clockwork</p>
    <a class="btn btn-outline" href="#">Learn More</a><a class="btn btn-contact" href="#">Contact</a>
  </div>
  <div class="service-card" style="left:848px">
    <svg width="64" height="64" viewBox="0 0 64 64" fill="none" stroke="#fff" stroke-width="2"><rect x="12" y="6" width="32" height="48"/><path d="M18 14h20M18 20h20M18 26h14M18 32h20"/><circle cx="44" cy="46" r="8"/><circle cx="44" cy="46" r="3"/></svg>
    <h3>Editorial Service/ Proofreading</h3>
    <p>Catching simple typos and grammatical faux pas to preserve your integrity</p>
    <a class="btn btn-outline" href="#">Learn More</a><a class="btn btn-contact" href="#">Contact</a>
  </div>
</section>

<section class="quote-band" role="img" aria-label="Soft peach-toned city skyline behind the tagline">
  <p class="script l1">If you want something done right...</p>
  <p class="script l2">find the right person to do it!</p>
</section>

<!-- feature: why me -->
<div class="feature-frame" style="left:558px;top:2214px;width:467px;height:271px"></div>
<div class="feature-photo" style="left:147px;top:2152px;width:544px;height:378px;background:linear-gradient(135deg,#3a352f,#6e5b49 50%,#a69a8e)" role="img" aria-label="Smiling woman on the phone at a laptop"></div>
<div class="feature-card" style="left:572px;top:2198px;width:469px;height:271px">
  <h3>Why Me?</h3>
  <p>I offer administrative, management, and editorial services for those in need of an expert, professional, and discreet “virtual” assistant. As an independent contractor</p>
  <a class="btn" href="#">Learn More</a>
</div>

<!-- feature: who benefits -->
<div class="feature-photo" style="left:498px;top:2615px;width:546px;height:378px;background:linear-gradient(135deg,#2d3640,#7f8c99 45%,#e1e4e8)" role="img" aria-label="Colleagues reviewing charts on a desk"></div>
<div class="feature-frame" style="left:133px;top:2677px;width:460px;height:271px"></div>
<div class="feature-card" style="left:147px;top:2661px;width:468px;height:272px">
  <h3>Who’s benefited from my help...</h3>
  <p>My employers and clients hail from backgrounds in , education, import/export businesses, IT, health and wellbeing and hospitality. They range from small to large businesses</p>
  <a class="btn" href="#">Learn More</a>
</div>

<!-- feature: what I can do -->
<div class="feature-frame" style="left:600px;top:3145px;width:441px;height:255px"></div>
<div class="feature-photo" style="left:161px;top:3085px;width:544px;height:369px;background:linear-gradient(135deg,#c9ced2,#6f7880 45%,#2e353b)" role="img" aria-label="Hands using a calculator beside a laptop keyboard"></div>
<div class="feature-card" style="left:587px;top:3129px;width:468px;height:271px">
  <h3>What I can do for you...</h3>
  <p>Sales accounting, inventory control, social media management, general office support, marketing assistance, client or HR relations, project management, contract reviews,</p>
  <a class="btn" href="#">Learn More</a>
</div>

<section class="calling">
  <h2>Sometimes your calling... well, it finds you!</h2>
  <p>I have over 30-years experience rescuing countless businesses from backlogs of work or faulty practices, and I have helped launched almost as many new businesses by building a solid foundation on sound systems. I have a history of arriving in just the right place</p>
  <a class="btn" href="#">Learn More</a>
</section>

<section class="testimonials">
  <h2>TESTIMONIALS</h2>
  <svg class="slider-arrow" style="left:96px" width="24" height="34" viewBox="0 0 24 34" fill="none" stroke="#9a9a9a" stroke-width="3"><path d="M20 2 5 17l15 15"/></svg>
  <div class="quote-card" style="left:161px">
    <div class="avatar" role="img" aria-label="Client portrait"></div>
    <p>Augiat in pede Fusce tellus Sed metus augue<br>convallis et vehicula ut pulvinar eu ante Integer<br>orci tellus tristique vitae consequat</p>
    <p class="author">By Author Name</p>
  </div>
  <div class="quote-card" style="left:610px">
    <div class="avatar" role="img" aria-label="Client portrait"></div>
    <p>Augiat in pede Fusce tellus Sed metus augue<br>convallis et vehicula ut pulvinar eu ante Integer<br>orci tellus tristique vitae consequat</p>
    <p class="author">By Author Name</p>
  </div>
  <svg class="slider-arrow" style="left:1068px" width="24" height="34" viewBox="0 0 24 34" fill="none" stroke="#9a9a9a" stroke-width="3"><path d="M4 2l15 15L4 32"/></svg>
</section>

<footer class="site-footer">
  <nav class="footer-nav">
    <a href="#">HOME</a><a href="#">ABOUT</a><a href="#">SERVICES</a><a href="#">FEES</a><a href="#">TESTIMONIALS</a><a href="#">CONTACT</a>
  </nav>
  <p class="legal">© 2020 Company Name | All Rights Reserved | Disclaimer</p>
  <div class="social" aria-label="Social links">
    <span><i></i></span><span><i></i></span><span><i></i></span><span><i></i></span>
  </div>
</footer>

</body>
</html>
```